Bluefern Business Services needs a new interactive and interesting website

We need an interesting, professional, modern and functional company website for Bluefern Business Services - a young IT Services company based out of Chennai, India.

Bluefern Business Services is a fully owned subsidiary of Marlow Goods, one of the world's leading direct to consumer wine merchant.

We already have a registered company logo which must feature in the website.

We conceive, design, develop, test, implement and support IT solutions across the entire Marlow Goods IT landscape. For ex : We currently run about 25 e-commerce websites for Marlow Goods on ATG and Dot Net.

We would like to see our corporate colors used in the website. (Burgundy wine and wine green - source: www.bluefernbs-site.com)

We are looking at this website to communicate a fun, friendly and professionally managed company - reaching out to career seekers, prospective customers and general public.

For reference - The company name 'Bluefern' is an inspiration from the Marlow Goods lineage.

The second image with the world map is stickered on our main entrance to the office, I am not sure where this can be used -just putting it out there..

Please note that there are only a few more days to submit designs for this contest  !

I would appreciate if you can help posting your designs in time for our review and consideration.

Thanks.

Reason: Thanks for your inputs. We have a number of designers and a lot to digest and work with in the past few days. There has been a rush of new designs in the last few days Hence we will require more time to process these and make our decision. Hence i am requesting the contest to be open for more days. Regards, Tarun

Target Market(s)

Prospective job seekers who want to know more about the company and also wish to apply for a job vacancy
People wanting to know more about the company in general and our progress
People who want to see what we offer and how we can help them too - prospective customers
Companies that are interested in our IT Captive journey and are looking for a business opportunity

Industry/Entity Type

E-Commerce

Requirements
Must have
• Log In/ Register facility acting as a Single Sign on for Intranet (Employees)

Facility to post job vacancies (with an expiry date) and enable people to apply for a role and upload their CV/Resume.

Facility to Review Job applications

Facility for website visitors to contact Bluefern business Services via an online 'Contact Us' form with a split of job seekers and business opportunities

Gallery facility to upload pictures regarding company events
Nice to have
• Less Cluttered and contemporary design
Some Wine/Vineyard inspirations will be good but not too much, the company is an IT services company

```html
<!DOCTYPE html>
<html lang="en">
<head>
<meta charset="utf-8">
<title>Bluefern Business Services</title>
<link href="https://fonts.googleapis.com/css2?family=Open+Sans:wght@300;400;600;700&display=swap" rel="stylesheet">
<style>
:root{
  --burgundy:#8a1d4a;
  --olive:#8c963a;
  --olive-dark:#6f7829;
  --nav:#3e3e3e;
  --footer:#4a4a4a;
  --text:#333;
  --muted:#8a8a8a;
  --line:#e3e3e3;
  --white:#fff;
}
*{box-sizing:border-box;margin:0;padding:0}
html,body{width:762px;height:1200px;overflow:hidden;background:var(--white);font-family:"Open Sans",sans-serif;color:var(--text)}
.page{position:relative;width:762px;height:1200px}
.abs{position:absolute}

.brand{left:70px;top:10px;display:flex;align-items:center;gap:6px;color:var(--burgundy)}
.brand-dot{width:16px;height:16px;border-radius:50%;background:var(--burgundy)}
.brand-name{font-size:27px;line-height:25px;letter-spacing:-.5px;font-weight:600}
.brand-sub{font-size:15px;line-height:18px;font-weight:400}

.toplinks{left:388px;top:25px;font-size:8px;color:var(--muted)}
.toplinks span{margin:0 4px}
.search{left:551px;top:20px;width:142px;height:19px;border:1px solid #d6d6d6;border-top:2px solid #c8c8c8;font-size:7px;color:#c4c4c4;padding:4px 5px}
.search-icon{position:absolute;right:6px;top:4px;width:8px;height:8px;border:1px solid #ccc;border-radius:50%}

.nav{left:70px;top:60px;width:622px;height:29px;background:linear-gradient(#4a4a4a,#333);display:flex;align-items:center}
.nav a{color:#eee;font-size:10px;text-decoration:none;height:29px;line-height:29px;text-align:center;white-space:nowrap;flex:none}
.nav a.active{background:var(--olive)}
.nav-social{margin-left:auto;margin-right:8px;display:flex;gap:5px;font-size:7px;color:#ddd}

.hero{left:70px;top:90px;width:622px;height:285px;background:linear-gradient(100deg,#5d7898 0%,#8fa6c0 14%,#d9dfe4 26%,#eef0ef 40%,#e4e6e4 52%,#2e3136 62%,#1f2226 72%,#a8b8c9 84%,#6e86a2 100%)}
.hero-panel{left:75px;top:182px;width:239px;height:126px;background:rgba(40,40,40,.72)}
.hero-title{left:75px;top:182px;height:29px;padding:0 6px;background:rgba(30,30,30,.85);color:var(--olive);font-size:22px;font-weight:300;line-height:29px;letter-spacing:.5px}
.hero-copy{left:82px;top:222px;width:230px;font-size:7.5px;line-height:10px;color:#eee}
.hero-copy p{margin-bottom:9px}
.btn-more{left:83px;top:282px;width:59px;height:19px;background:var(--olive);color:#fff;font-size:9px;line-height:19px;text-align:center}

.welcome{left:0;top:400px;width:762px;text-align:center;font-size:17px;font-weight:300;line-height:20px;color:#6e6e6e}
.welcome em{font-style:normal;color:var(--olive)}

.svc-label{font-size:9px;color:#222;text-align:center;width:160px;line-height:11px}

.divider{left:70px;width:622px;height:1px;background:var(--line)}

.apply{left:72px;top:690px;width:210px;height:228px;background:var(--olive);border-radius:2px;box-shadow:1px 2px 3px rgba(0,0,0,.25)}
.apply h2{position:absolute;left:8px;top:6px;font-size:13px;font-weight:400;color:#fff}
.apply-rule{position:absolute;left:8px;right:8px;top:29px;height:1px;background:rgba(255,255,255,.35)}
.field{position:absolute;left:9px;width:193px;height:19px;background:#fff;border:1px solid #6b7425;font-size:9px;color:#444;padding:3px 8px}
.btn-register{position:absolute;left:8px;top:194px;width:95px;height:26px;background:var(--olive-dark);color:#fff;font-size:11px;line-height:26px;text-align:center;border-radius:2px;box-shadow:inset 0 1px 0 rgba(255,255,255,.2)}

.vline{left:336px;top:704px;width:1px;height:208px;background:var(--line)}
.gallery-title{left:365px;top:692px;font-size:12px;color:#222;font-weight:400}
.upload{left:595px;top:696px;font-size:8px;color:#666;text-decoration:underline}
.thumb{width:140px;height:92px;border-bottom:4px solid var(--olive);box-shadow:0 1px 3px rgba(0,0,0,.3)}

.customers-title{left:70px;top:944px;font-size:12px;color:#222;font-weight:400}
.logos{left:70px;top:970px;width:622px;height:52px;border-top:1px solid var(--line);border-bottom:1px solid var(--line);display:flex}
.logos div{display:flex;align-items:center;justify-content:center;gap:6px;font-size:9px;font-weight:600;color:#7a7a7a;border-right:1px solid var(--line)}
.logos div:last-child{border-right:none}
.logo-mark{width:10px;height:10px;background:#9a9a9a;border-radius:50%}

.footer{left:70px;top:1032px;width:622px;height:168px;background:var(--footer)}
.foot-head{height:19px;background:#333;color:#eee;font-size:11px;line-height:19px;text-align:center;border-radius:2px}
.foot-list{list-style:none;font-size:9px;color:#ccc}
.foot-list li{height:14px;line-height:14px;border-bottom:1px solid #565656;padding-left:8px;position:relative}
.foot-list li::before{content:"";position:absolute;left:0;top:5px;border-left:3px solid #ddd;border-top:2px solid transparent;border-bottom:2px solid transparent}
.foot-list li.current{color:var(--burgundy)}
.svc-list li{border-bottom:none;height:15px;line-height:15px;font-size:10px;color:#eee}
.foot-brand{left:371px;top:1045px;width:121px;height:31px;background:#333;color:#eee;padding:0 10px;line-height:14px}
.foot-brand b{font-size:17px;font-weight:600;display:block;line-height:18px}
.foot-brand small{font-size:10px;display:block;line-height:11px}
.foot-about{left:371px;top:1083px;width:160px;font-size:10px;line-height:14px;color:#eee}
.updated{left:568px;top:1058px;color:#eee;font-size:9px;font-weight:600;display:flex;align-items:center;gap:4px}
.updated small{display:block;font-size:5.5px;font-weight:600}
.updated i{width:14px;height:14px;border-radius:50%;background:#bbb;display:block}
.email{left:566px;top:1082px;width:112px;height:17px;background:#fff;border-radius:2px;font-size:6.5px;color:#999;padding:3px 10px;font-style:italic}
.foot-social{left:566px;top:1108px;width:118px;display:flex;flex-wrap:wrap;gap:3px 7px;font-size:8px;color:#ddd}
.foot-social span{display:flex;align-items:center;gap:3px}
.foot-social span::before{content:"";width:8px;height:8px;border-radius:2px;background:#3a9fd8}
.copy-rule{left:70px;top:1176px;width:622px;height:1px;background:#5c5c5c}
.copy{left:70px;top:1184px;width:622px;text-align:center;font-size:8px;color:#eee}
</style>
</head>
<body>
<div class="page">

  <header>
    <div class="abs brand"><span class="brand-dot"></span><div><div class="brand-name">bluefern</div><div class="brand-sub">Business Services</div></div></div>
    <div class="abs toplinks">Extranet Login<span>|</span>Driftsstatus<span>|</span>Hotline</div>
    <div class="abs search">Search...<span class="search-icon"></span></div>
    <nav class="abs nav">
      <a class="active" style="width:71px">Home</a>
      <a style="width:84px">About us</a>
      <a style="width:72px">Clients</a>
      <a style="width:76px">Services</a>
      <a style="width:80px">Careers</a>
      <a style="width:86px">Contact us</a>
      <div class="nav-social"><span>Pagebook</span><span>Chirpline</span><span>Linkwork</span></div>
    </nav>
  </header>

  <section>
    <div class="abs hero" role="img" aria-label="Business presenter pointing at a rising chart on a world map board in a bright office with colleagues watching"></div>
    <div class="abs hero-panel"></div>
    <div class="abs hero-title">BLUEFERN</div>
    <div class="abs hero-copy">
      <p>Lorem ipsum dolor sit amet, consectetur adipisicing elit, sed do eiusmod tempor incididunt ut labore et dolore magna aliqua.</p>
      <p>Ut enim ad minim veniam, quis nostrud exercitation ullamco laboris nisi ut aliquip ex ea commodo consequat...</p>
    </div>
    <div class="abs btn-more">Read More</div>
  </section>

  <div class="abs welcome">Welcome to <em>Bluefern</em> Business Services, an<br>emerging provider of global IT consulting and....</div>

  <svg class="abs" style="left:0;top:450px" width="762" height="230" viewBox="0 450 762 230" aria-hidden="true">
    <defs>
      <radialGradient id="globe" cx="40%" cy="38%" r="62%"><stop offset="0" stop-color="#e6f4fd"/><stop offset=".5" stop-color="#7cc0ea"/><stop offset="1" stop-color="#2379bf"/></radialGradient>
      <radialGradient id="shopper" cx="45%" cy="40%" r="65%"><stop offset="0" stop-color="#d9a98c"/><stop offset=".55" stop-color="#8c3a48"/><stop offset="1" stop-color="#2b1a22"/></radialGradient>
      <radialGradient id="commerce" cx="55%" cy="45%" r="65%"><stop offset="0" stop-color="#c6e57f"/><stop offset=".6" stop-color="#6aab34"/><stop offset="1" stop-color="#3b4a33"/></radialGradient>
      <radialGradient id="tiles" cx="50%" cy="50%" r="60%"><stop offset="0" stop-color="#3d6f99"/><stop offset=".6" stop-color="#22344a"/><stop offset="1" stop-color="#0e1620"/></radialGradient>
    </defs>
    <path d="M28 602 C120 520 220 480 330 478 C450 476 560 470 738 498" fill="none" stroke="#d6d6d6" stroke-width="1" stroke-dasharray="2 3"/>
    <circle cx="28" cy="602" r="6" fill="#fff" stroke="#ccc"/>
    <circle cx="738" cy="498" r="6" fill="#fff" stroke="#ccc"/>

    <g stroke="#e6e6e6" fill="#fff">
      <circle cx="148" cy="562" r="62"/><circle cx="286" cy="520" r="60"/>
      <circle cx="424" cy="564" r="60"/><circle cx="594" cy="552" r="90"/>
    </g>
    <circle cx="148" cy="562" r="52" fill="url(#shopper)" role="img" aria-label="Shopper with bags holding a payment card"/>
    <circle cx="286" cy="520" r="52" fill="url(#commerce)" role="img" aria-label="Green keyboard key with a shopping cart"/>
    <circle cx="424" cy="564" r="52" fill="url(#tiles)" role="img" aria-label="Wall of colourful app tiles"/>
    <circle cx="594" cy="552" r="76" fill="url(#globe)" role="img" aria-label="Blue jigsaw puzzle globe"/>

    <g fill="#8a1d4a" stroke="#fff" stroke-width="2">
      <circle cx="90" cy="566" r="21"/><circle cx="331" cy="488" r="21"/>
      <circle cx="455" cy="613" r="21"/><circle cx="670" cy="518" r="21"/>
    </g>
    <g fill="#fff">
      <path d="M82 570 l10 -10 h6 v6 l-10 10 z"/>
      <path d="M322 486 h18 l-3 10 h-12 z"/><path d="M325 486 l6 -7 l6 7" fill="none" stroke="#fff" stroke-width="1.6"/>
      <g><rect x="447" y="605" width="4" height="4"/><rect x="453" y="605" width="4" height="4"/><rect x="459" y="605" width="4" height="4"/>
      <rect x="447" y="611" width="4" height="4"/><rect x="453" y="611" width="4" height="4"/><rect x="459" y="611" width="4" height="4"/>
      <rect x="447" y="617" width="4" height="4"/><rect x="453" y="617" width="4" height="4"/><rect x="459" y="617" width="4" height="4"/></g>
      <circle cx="666" cy="515" r="7"/><circle cx="675" cy="524" r="5"/>
    </g>
    <circle cx="666" cy="515" r="2.5" fill="#8a1d4a"/><circle cx="675" cy="524" r="2" fill="#8a1d4a"/>
  </svg>

  <div class="abs svc-label" style="left:70px;top:634px">Packaged Applications</div>
  <div class="abs svc-label" style="left:213px;top:594px">Digital Commerce</div>
  <div class="abs svc-label" style="left:345px;top:644px">Enterprise Application<br>Integration</div>
  <div class="abs svc-label" style="left:523px;top:654px">Application Development<br>&amp; Maintenance</div>

  <div class="abs divider" style="top:681px"></div>

  <form class="abs apply">
    <h2>Apply For A Job</h2>
    <div class="apply-rule"></div>
    <div class="field" style="top:40px">Your Name *</div>
    <div class="field" style="top:73px">Your Phone Number *</div>
    <div class="field" style="top:107px">Your Address *</div>
    <div class="field" style="top:140px;height:44px">Your Comment *</div>
    <div class="btn-register">Register</div>
  </form>

  <div class="abs vline"></div>
  <section>
    <h2 class="abs gallery-title">Our Gallery</h2>
    <div class="abs upload">Upload Picture</div>
    <div class="abs thumb" style="left:365px;top:718px;background:linear-gradient(100deg,#f2f4f5 0%,#c9d0d5 25%,#e8d2c2 55%,#6fa0c4 80%,#dfe4e6 100%)" role="img" aria-label="Smiling student at a computer"></div>
    <div class="abs thumb" style="left:520px;top:718px;background:linear-gradient(100deg,#7c5048 0%,#c99e8c 22%,#4f5458 45%,#c7b8a8 70%,#8c8a88 100%)" role="img" aria-label="Students working in a computer lab"></div>
    <div class="abs thumb" style="left:365px;top:828px;background:linear-gradient(100deg,#d98f7a 0%,#a4443c 25%,#3c2c2a 50%,#c9936a 75%,#6c4a42 100%)" role="img" aria-label="Group of students gathered around a laptop"></div>
    <div class="abs thumb" style="left:520px;top:828px;background:linear-gradient(100deg,#f1f4f5 0%,#55606a 22%,#dcdfe0 45%,#d9aa8e 70%,#edeeee 100%)" role="img" aria-label="Colleagues looking at a monitor"></div>
  </section>

  <div class="abs divider" style="top:929px"></div>

  <h2 class="abs customers-title">Customer's Logo</h2>
  <div class="abs logos">
    <div style="width:94px"><span class="logo-mark"></span>Vekora</div>
    <div style="width:98px"><span class="logo-mark"></span>Pagebook</div>
    <div style="width:96px"><span class="logo-mark"></span>Circlenet</div>
    <div style="width:94px"><span class="logo-mark"></span>Zentra</div>
    <div style="width:117px"><span class="logo-mark"></span>Clipstream</div>
    <div style="width:123px"><span class="logo-mark"></span>Travelnote</div>
  </div>

  <footer>
    <div class="abs footer"></div>
    <div class="abs foot-head" style="left:82px;top:1050px;width:93px">Navigation</div>
    <ul class="abs foot-list" style="left:90px;top:1080px;width:96px">
      <li class="current">Home</li><li>About us</li><li>Clients</li><li>Services</li><li>Careers</li><li>Contact us</li>
    </ul>
    <div class="abs foot-head" style="left:230px;top:1050px;width:93px">Services</div>
    <ul class="abs foot-list svc-list" style="left:232px;top:1079px;width:125px">
      <li>Packaged Applications</li><li>Digital Commerce</li><li>Enterprise Application</li><li>Development</li>
    </ul>
    <div class="abs foot-brand"><b>bluefern</b><small>Business Services</small></div>
    <p class="abs foot-about">Lorem ipsum dolor sit amet, consectetur adipisicing elit, sed do eiusmod tempor incididunt ut labore et dolore magna aliqua.</p>
    <div class="abs updated"><i></i><div>GET UPDATED<small>SUBSCRIBE NOW</small></div></div>
    <div class="abs email">email@domain.com</div>
    <div class="abs foot-social"><span>Vidra</span><span>Pagebook</span><span>Chirpline</span><span>Callwave</span></div>
    <div class="abs copy-rule"></div>
    <div class="abs copy">Copyright 2014 © Bluefern All rights reserved.</div>
  </footer>

</div>
</body>
</html>
```